Android App Design Project

Hi my name is Nadir, and I'm an android developer. I'm searching for a professional designer that can design my app.I have already launched the app and you can find it in the apptrove bazaar.

Main Requirements
- 15 sport icons
- 6 android pages
- Action bar
- Buttons and other icons

You need to do all requirements to submit a design. I need the design in both JPEG format and Photoshop PSD format. If you are interested then please download the PDF file ,it will help you a lot.
The name of the app is "MATCH VIEW Classic" you can find it in Orbix Shelf.

NOTICE: You might read that the Payment is not guaranteed if I'm not happy with the design BUT if you make a good design and you win the contest, then you become my main designer that means if I want to change or add something to the design of the app in the future I return to you "the winner" directly to make the redesign and get paid for it.

Regards.
Skype: Fadi Hamoudi "fadi48"
E-mail: fadinadir@quillpost.net

Industry/Entity Type

Tv

Requirements
Must have
• - 15 sport icons
- 6 android pages
- Action bar
- Buttons and other icons

```html
<!DOCTYPE html>
<html lang="en">
<head>
<meta charset="utf-8">
<title>Sports tv</title>
<link rel="stylesheet" href="https://fonts.googleapis.com/css2?family=Ubuntu:ital,wght@0,400;0,500;0,700;1,700&display=swap">
<style>
  :root {
    --bar-top: #f7803f;
    --bar-bottom: #e25a14;
    --bar-line: #c9500f;
    --bar-divider: rgba(255,255,255,0.35);
    --screen: #262624;
    --screen-light: #2e2e2b;
    --grid-line: #4a4a46;
    --btn-top: #2b8c7e;
    --btn-bottom: #166356;
    --tile-top: #2f5272;
    --tile-bottom: #22405c;
    --tile-edge: #15293c;
    --silhouette: #dfe8f0;
    --text-light: #ffffff;
    --label: #dde4ea;
  }
  * { margin: 0; padding: 0; box-sizing: border-box; }
  html, body { width: 817px; height: 1200px; overflow: hidden; }
  body {
    font-family: "Ubuntu", sans-serif;
    background: radial-gradient(circle at 50% 40%, var(--screen-light), var(--screen));
    position: relative;
  }
  .action-bar {
    position: absolute; left: 0; top: 0; width: 817px; height: 102px;
    background: linear-gradient(var(--bar-top), var(--bar-bottom));
    border-bottom: 3px solid var(--bar-line);
  }
  .app-title {
    position: absolute; left: 10px; top: 26px;
    font-size: 41px; font-weight: 500; color: var(--text-light);
  }
  .bar-divider { position: absolute; top: 0; width: 2px; height: 102px; background: var(--bar-divider); }
  .info-icon {
    position: absolute; left: 574px; width: 116px; top: 14px; text-align: center;
    font-size: 62px; font-style: italic; font-weight: 700; color: var(--text-light);
    font-family: Georgia, serif;
  }
  .settings-icon { position: absolute; left: 733px; top: 23px; width: 56px; height: 56px; }
  .tab-button {
    position: absolute; top: 146px; width: 209px; height: 74px;
    background: linear-gradient(var(--btn-top), var(--btn-bottom));
    border-radius: 10px; box-shadow: 0 3px 6px rgba(0,0,0,0.5);
    color: var(--text-light); font-size: 42px; font-weight: 700;
    display: flex; align-items: center; justify-content: center;
  }
  .grid-h { position: absolute; left: 0; width: 817px; height: 3px; background: var(--grid-line); }
  .grid-v { position: absolute; left: 397px; top: 319px; width: 3px; height: 881px; background: var(--grid-line); }
  .sport-tile {
    position: absolute; width: 176px; height: 174px;
    background: linear-gradient(var(--tile-top), var(--tile-bottom));
    border: 2px solid var(--tile-edge); border-radius: 16px;
    box-shadow: 0 3px 8px rgba(0,0,0,0.55);
  }
  .sport-figure {
    position: absolute; left: 58px; top: 18px; width: 58px; height: 90px;
    background: linear-gradient(var(--silhouette), #b9c8d6); border-radius: 28px 28px 12px 12px; opacity: 0.9;
  }
  .sport-label {
    position: absolute; left: 0; right: 0; bottom: 18px; text-align: center;
    font-size: 25px; color: var(--label);
  }
</style>
</head>
<body>
  <header class="action-bar">
    <div class="app-title">Sports tv</div>
    <div class="bar-divider" style="left:574px"></div>
    <div class="bar-divider" style="left:690px"></div>
    <div class="info-icon">i</div>
    <svg class="settings-icon" viewBox="0 0 56 56" aria-label="Settings">
      <g fill="#ffffff" transform="translate(28 28)">
        <rect x="-6" y="-28" width="12" height="14" rx="2"/>
        <rect x="-6" y="-28" width="12" height="14" rx="2" transform="rotate(45)"/>
        <rect x="-6" y="-28" width="12" height="14" rx="2" transform="rotate(90)"/>
        <rect x="-6" y="-28" width="12" height="14" rx="2" transform="rotate(135)"/>
        <rect x="-6" y="-28" width="12" height="14" rx="2" transform="rotate(180)"/>
        <rect x="-6" y="-28" width="12" height="14" rx="2" transform="rotate(225)"/>
        <rect x="-6" y="-28" width="12" height="14" rx="2" transform="rotate(270)"/>
        <rect x="-6" y="-28" width="12" height="14" rx="2" transform="rotate(315)"/>
        <circle r="19"/>
      </g>
      <circle cx="28" cy="28" r="8" fill="var(--bar-bottom)"/>
    </svg>
  </header>

  <div class="tab-button" style="left:133px">News</div>
  <div class="tab-button" style="left:488px">Score</div>

  <div class="grid-h" style="top:319px"></div>
  <div class="grid-h" style="top:625px"></div>
  <div class="grid-h" style="top:932px"></div>
  <div class="grid-v"></div>

  <div class="sport-tile" style="left:64px;top:368px">
    <div class="sport-figure" role="img" aria-label="Badminton player silhouette"></div>
    <div class="sport-label">Badminton</div>
  </div>
  <div class="sport-tile" style="left:572px;top:368px">
    <div class="sport-figure" role="img" aria-label="Ice hockey player silhouette"></div>
    <div class="sport-label">Ice Hocky</div>
  </div>
  <div class="sport-tile" style="left:64px;top:677px">
    <div class="sport-figure" role="img" aria-label="Tennis player silhouette"></div>
    <div class="sport-label">Tennis</div>
  </div>
  <div class="sport-tile" style="left:572px;top:677px">
    <div class="sport-figure" role="img" aria-label="Cricket batsman silhouette"></div>
    <div class="sport-label">Cricket</div>
  </div>
  <div class="sport-tile" style="left:64px;top:988px">
    <div class="sport-figure" role="img" aria-label="Basketball player silhouette"></div>
    <div class="sport-label">Basketball</div>
  </div>
  <div class="sport-tile" style="left:572px;top:988px">
    <div class="sport-figure" role="img" aria-label="Handball player silhouette"></div>
    <div class="sport-label">Handball</div>
  </div>
</body>
</html>
```